Business Card Design

WE are looking for a premium quality Business Cards for a Law Firm . Copies of our current business card is attached.

Contact Information for Business Card

xyz

```html
<!DOCTYPE html>
<html lang="en">
<head>
<meta charset="utf-8">
<title>Ashford Lawyers – Business Cards</title>
<link href="https://fonts.googleapis.com/css2?family=Arimo:wght@400;700&family=Cinzel:wght@600;700&display=swap" rel="stylesheet">
<style>
  :root {
    --green: #0e3b2a;
    --gold: #b4955a;
    --paper: #f6f6f4;
    --ink: #2b2b2b;
    --white: #ffffff;
    --backdrop: #d9d9d6;
    --serif: "Cinzel", Georgia, serif;
    --sans: "Arimo", Arial, sans-serif;
  }
  * { box-sizing: border-box; margin: 0; padding: 0; }
  html, body { width: 1200px; height: 912px; overflow: hidden; }
  body { background: var(--backdrop); position: relative; font-family: var(--sans); }

  .card {
    position: absolute;
    width: 640px; height: 366px;
    box-shadow: 0 8px 24px rgba(0,0,0,.18);
    overflow: hidden;
  }

  .brand__ring {
    width: 60px; height: 60px; border-radius: 50%;
    border: 2px solid var(--white); margin: 0 auto 12px;
  }
  .brand__name { font-family: var(--serif); font-weight: 700; letter-spacing: 2px; white-space: nowrap; }

  /* Back: office locations */
  .card--back { left: 150px; top: 60px; background: var(--green); color: var(--white); }
  .card--back .brand { position: absolute; top: 34px; left: 0; right: 0; text-align: center; }
  .card--back .brand__name { font-size: 26px; }
  .offices { position: absolute; left: 40px; right: 40px; bottom: 40px; display: flex; align-items: flex-end; }
  .office { flex: 1; text-align: center; font-size: 12px; line-height: 1.35; }
  .office h3 { font-size: 14px; font-weight: 700; margin-bottom: 2px; }
  .office b { font-weight: 700; }
  .office + .office { border-left: 1px solid rgba(255,255,255,.45); }
  .office:nth-child(2) { padding-top: 24px; margin-bottom: 28px; }
  .office:nth-child(3) { padding-top: 20px; margin-bottom: 56px; }

  /* Front: personal details */
  .card--front { left: 410px; top: 486px; background: var(--paper); color: var(--ink); }
  .card--front .brand { position: absolute; top: 24px; right: 36px; text-align: center; width: 274px; }
  .card--front .brand__ring { border-color: var(--gold); width: 54px; height: 54px; margin-bottom: 10px; }
  .card--front .brand__name { color: var(--green); font-size: 22px; letter-spacing: 1.5px; }
  .rule-top { position: absolute; left: 330px; right: 36px; top: 132px; border-top: 1px solid var(--ink); }
  .address { position: absolute; right: 36px; top: 142px; text-align: right; font-size: 15px; line-height: 1.3; }
  .person { position: absolute; left: 36px; top: 150px; }
  .person__name { font-family: var(--serif); font-weight: 700; font-size: 24px; color: var(--green); letter-spacing: .5px; }
  .person__role { color: var(--gold); font-size: 14px; line-height: 1.3; margin-top: 2px; }
  .person__rule { width: 300px; border-top: 1px solid var(--ink); margin: 8px 0 6px; }
  .contacts { list-style: none; font-size: 15px; line-height: 1.25; }
  .contacts li { display: flex; align-items: center; gap: 10px; }
  .contacts svg { width: 13px; height: 13px; fill: var(--green); flex: none; }
  .band-gold { position: absolute; left: 0; right: 0; bottom: 24px; height: 3px; background: var(--gold); }
  .band-green { position: absolute; left: 0; right: 0; bottom: 0; height: 18px; background: var(--green); }
</style>
</head>
<body>

<section class="card card--back" aria-label="Business card back">
  <div class="brand">
    <div class="brand__ring"></div>
    <div class="brand__name">ASHFORD LAWYERS</div>
  </div>
  <div class="offices">
    <div class="office">
      <h3>Melbourne</h3>
      Level 12, 48 Harbour Lane<br>Melbourne, VIC 3000<br><b>Phone :</b> +61 03 5550 1234
    </div>
    <div class="office">
      <h3>Sydney</h3>
      Level 9, Kingsley Building<br>22 Market Row<br>Parramatta, NSW 2150<br><b>Phone :</b> +61 02 5550 2345
    </div>
    <div class="office">
      <h3>Perth</h3>
      Level 18, Orion Tower<br>75 Riverside Drive<br>Perth, WA 6000<br><b>Phone :</b> +61 08 5550 3456
    </div>
  </div>
</section>

<section class="card card--front" aria-label="Business card front">
  <div class="brand">
    <div class="brand__ring"></div>
    <div class="brand__name">ASHFORD LAWYERS</div>
  </div>
  <div class="rule-top"></div>
  <p class="address">Level 3, Ashford House<br>210 Ridge Terrace<br>Spring Hill, QLD 4000</p>

  <div class="person">
    <h1 class="person__name">DANIEL MERCER</h1>
    <p class="person__role">Director &amp; Principal Solicitor<br>MBA, Juris Doctor</p>
    <div class="person__rule"></div>
    <ul class="contacts">
      <li><svg viewBox="0 0 16 16"><path d="M3 1l3 3-1.5 2a9 9 0 0 0 5.5 5.5L12 10l3 3-2 2C7 15 1 9 1 3z"/></svg>+61 7 5550 4567</li>
      <li><svg viewBox="0 0 16 16"><path d="M4 1h8a1 1 0 0 1 1 1v12a1 1 0 0 1-1 1H4a1 1 0 0 1-1-1V2a1 1 0 0 1 1-1zm1 2v9h6V3z"/></svg>+61 0400 555 678</li>
      <li><svg viewBox="0 0 16 16"><path d="M1 3h14v10H1zm1.5 1.5L8 9l5.5-4.5z"/></svg>daniel@ashfordlawyers.com.au</li>
      <li><svg viewBox="0 0 16 16"><circle cx="8" cy="8" r="7"/></svg>www.ashfordlawyers.com.au</li>
    </ul>
  </div>

  <div class="band-gold"></div>
  <div class="band-green"></div>
</section>

</body>
</html>
```